Website front end design for an education nonprofit

This project involves design and development of the website front end (i.e., Web user interface and user experience design) for TAVO Sphere, a nonprofit initiative for developing an online platform for basic English language instruction, especially targeted toward underprivileged, non-native English speaking populations.

More about us: We are a team of educators, researchers and engineers passionate about this cause and would like to invite talented, creative web developers to join us in this effort to create positive social impact! Please send a personal message to the project owner for the executive summary to get more information about our initiative, big picture vision and the team.

TAVO Sphere website front end (UI/UX) design
Our key goals for this project are to develop an impressive Drupal-based front end for our website as well as to find really talented and creative web/UI/UX designers-cum-developers who are experts in the state-of-the-art web technologies, and are passionate about the cause of global online basic education. At the end of this project, we hope to have long term engagement with the selected developer(s) for our future website design and development needs.

Here are some preliminary guidelines on the TAVO Sphere website front end framework as envisioned by us so far. Please note that we would very much encourage creative ideas and mock-ups from the developers.

1. Current platform: Our website prototype back-end uses Drupal CMS (we plan to continue using Drupal CMS) and at the moment, a toy front-end is based on the Drupal Skeleton platform for its simplicity, clean UI and mobile device friendliness. The web developer / designer can choose any Drupal front end as a starting point or come up with a new Drupal template that meets our requirements below. Prior experience and expertise on Drupal would be great.

2. Audience profile: While the primary audience for the website is expected to be young kids (6-10 years) not very familiar with English, the secondary audience also includes adults interested in basic English language skills. So the overall goal is to have simple, uncluttered / clean, elegant and lightweight (think loading time as well as mobile device friendliness) interface that is extremely intuitive and easy to navigate, is artistic and aesthetically appealing to a wide audience (especially the non-native English speaking populations). The most important point is that our target audience should feel welcome with the clean, crisp look and easy, user-centric navigation, and should in no case feel overwhelmed (say with too much text or clutter on the front page).

3. Front page: Here is a currently envisioned preliminary sketch of the website front page (very much open for refinement and improvements)
a. The top “menu bar” part of the landing page will have our organization name and logo along with (or above) the top menu bar with the following links and sub-links
i. “Learn” link with sub-menu of all our content sections (World learning, Basic sentence learning, Classic short stories, Picture Dictionary)
ii. “About” links with information about us (sub-menu entries: About TAVO Sphere, Team, Supporters, Contributors)
iii. “Contribute” link with sub-menu entries Donate, Volunteer
iv. Menu entries towards the right side: “Login / sign up” followed by
v. “Search” with space to enter the search phrase
b. The middle “main page content” part of the page is where we would have entry points to our main content categories. The portion is envisioned to be graphical, with big blocks (images) as links to our content categories. The current categories (to start with) include 1. Word learning, 2. Basic sentence learning, and 3. Classic stories. We welcome creative ideas to represent these content categories in an appealing and elegant way (for example, these content categories could be portrayed as closed double doors that lead to the pages with the content. We would like to have placeholders for appropriate image links to different content categories – we should be able to put appropriate images or change them as we come up with new ideas that would work best with our target audience). The categories would change and grow as our content evolves, hence the core idea is to build a flexible framework that readily allows for expansion as well as customization.
c. The bottom menu / links bar portion of the landing page will have a list of links that are not included at the top. Examples include (with flexibility needed to add more when needed)
i. “Help”: this leads to a new page with FAQ, How to use
ii. “Contact us” link to a web contact form page
iii. “For Teachers” link to a page with information such as how to use, tips, pilot programs,
iv. “Volunteer” link to page with links such as Donate, Volunteer
v. “Contributors” that would link to a page with information about our Artists, Teachers, Writers, Developers etc.
vi. “Jobs” would link to a jobs page
vii. “Blog” would lead to our blog page
viii. “User stories” link to pages with feedback that we obtain from the users about how the content has helped them,
ix. Web 2.0 placeholders for social media (to be added later)

d. The footer of the website should include text “2013 TAVO Sphere, All rights reserved.”

4. The middle block of the front page is the largest in screen real estate and perhaps the most challenging part that requires much creativity and thought on the UI/UX design aspect – the content pages pointed to by the section links on the middle portion of the front page are also being designed.

5. Color preference is towards soft, elegant (think grays, whites, light blues, other light colors) web safe colors. No harsh (too bright, garish) colors.

6. Fonts preference Nice, clean looking fonts (Arial alright) compatible across browsers.

7. Portability and robustness of the front page layout for different platforms should be carefully considered. Although our first launch target platform is PC (where cross browser compatibility is important), this would very soon be followed by mobile devices such as tablets and smartphones given their prevalence across the globe. This mobile friendly design or easy portability to mobile platforms with little work requirement should be considered as a design requirement.

8. Front page as a framework for the complete website: Note that the top and the bottom portions of the front page are envisioned be used as a common template / frame across all the pages of our website – the middle portion would be used to show our content on the other pages of our website.

9. UX: For the UI/UX design, it is critical to keep in mind key qualities such as ease of use, simplicity, elegance and artistic appeal. Some specific points to keep in mind: (1) the major portion of the target audience would be new to English and (2) young children are expected to be the primary audience but we want the website to appeal to adults interested in learning as well, and (3) we need the website to work even with relatively slow Internet speeds (for underdeveloped / developing regions especially), should always be kept in mind. HTML5 compliance ideas are encouraged.

10. Strictly not desired: Typical corporate feel seen in many webpages, blocky graphics, dull and uninviting overall look with no personality, Flash type effects, harsh colors.

11. Creativity and imagination necessary: We would like to reiterate that the designer/developer has complete freedom to re-imagine the front page considering the above requirements and get back with ideas for an inspiring layout that presents the content outlined above in an intuitive format, carefully considering our target audience.

A note: As a rule, we will always make sure that our developers and artists get proper credit for their work and are recognized and acknowledged by everyone visiting our website.

Expected deliverables:
Website design psd files AND coded webpage / Drupal template: the corresponding source code and all the required libraries, images etc would be required with minimal documentation / pointers on how to make changes and customizations.

Interested developers are encouraged to first send us preliminary prototype Design for the front page to get feedback on whether their approach and style is in line with our needs and preferences. We will suggest the developers to proceed further if the team thinks there is some potential for a match (of course, the final determination would be from the pool of shortlisted submissions) – otherwise, in case the team does not see potential for a match with our needs or if we have already received multiple submissions that are comparatively more closely aligned with our vision for the website, we'd prefer to be respectful of the developers’ time and effort by requesting them not to proceed further.

Please consider this effort as your contribution to an important social cause of global and accessible online education and not a commercial enterprise (our passion for making a positive impact is what is driving the TAVO Sphere nonprofit team to undertake this initiative!). We would like to invite you to join us in this effort!

Project Deadline Extended
Reason: Due to requests from interested designers, we are extending the deadline. Looking forward to receiving many other creative designs!

Please see the project brief.

Real Estate

• Please see the project brief.

```html
<!DOCTYPE html>
<html lang="en">
<head>
<meta charset="utf-8">
<title>TAVO Sphere – English learning for everyone</title>
<link href="https://fonts.googleapis.com/css2?family=Source+Sans+3:ital,wght@0,400;0,600;0,700;1,400&display=swap" rel="stylesheet">
<style>
:root{
  --ink:#3d3d3d;
  --muted:#6b6b6b;
  --accent:#1ea2d6;
  --accent-dark:#1487bd;
  --teal:#2f8fb3;
  --teal-panel:#3a97bb;
  --footer:#3b93b4;
  --footer-deep:#2d81a2;
  --dark-card:rgba(18,18,18,.92);
  --arrow-box:#2b7ea3;
  --band-top:#ffffff;
  --band-bottom:#e9e9e9;
  --white:#ffffff;
}
*{box-sizing:border-box;margin:0;padding:0}
html,body{width:958px;height:1200px;overflow:hidden;background:var(--white)}
body{font-family:"Source Sans 3",Arial,sans-serif;color:var(--ink);position:relative}
a{color:inherit;text-decoration:none}
.abs{position:absolute}

/* header */
.site-header{position:absolute;left:0;top:0;width:958px;height:67px;background:var(--white)}
.brand{left:144px;top:20px;font-size:25px;font-weight:600;color:#555;letter-spacing:-.3px}
.main-nav a{position:absolute;top:30px;font-size:8.5px;font-weight:700;color:#444}
.search{left:530px;top:25px;width:148px;height:19px;background:#eeeeee;border:1px solid #dcdcdc;font-size:7px;color:#999;padding:5px 8px}
.search svg{position:absolute;right:6px;top:3px}
.btn-top{top:25px;height:19px;width:60px;background:linear-gradient(#2db0e6,#1690cc);color:#fff;font-size:7.5px;text-align:center;line-height:19px;border:1px solid #1683b8}

/* hero */
.hero{left:0;top:67px;width:958px;height:417px;background:linear-gradient(160deg,#a7b870 0%,#6d8f3e 30%,#c9a69a 48%,#4f6f2c 70%,#8aa55a 100%)}
.hero-arrow{top:250px;width:50px;height:50px;border-radius:50%;background:rgba(40,40,40,.35)}
.hero-arrow svg{position:absolute;left:18px;top:16px}
.category{top:409px;width:222px;height:69px;background:var(--dark-card)}
.category h2{position:absolute;left:15px;top:11px;font-size:13.5px;font-weight:600;color:var(--accent)}
.category p{position:absolute;left:15px;top:33px;width:150px;font-size:7px;line-height:12px;color:#eee}
.category .go{position:absolute;right:0;bottom:0;width:45px;height:42px;background:var(--arrow-box)}
.category .go svg{position:absolute;left:16px;top:14px}

/* mission band */
.mission{left:0;top:484px;width:958px;height:84px;background:linear-gradient(var(--band-top),var(--band-bottom))}
.mission h1{position:absolute;left:145px;top:13px;font-size:16.5px;font-weight:400;color:var(--accent)}
.mission p{position:absolute;left:144px;top:40px;width:540px;font-size:8.3px;line-height:15px;color:#444}
.btn-join{left:698px;top:510px;width:116px;height:32px;background:linear-gradient(#2fb3ea,#1a92cf);color:#fff;font-size:9.5px;text-align:center;line-height:32px;border:1px solid #1585bd}

/* welcome */
.section-title{font-size:16px;font-weight:400;color:var(--teal)}
.photo{background:linear-gradient(135deg,#d9c6be,#b98f83 45%,#ece9e7)}
.welcome-text{left:346px;top:617px;width:172px;font-size:7px;line-height:12.4px;color:#666}
.learn-card{left:541px;top:594px;width:273px;height:122px}
.learn-photo{position:absolute;left:0;top:0;width:137px;height:122px;background:linear-gradient(120deg,#3f3a36,#8d6c55 50%,#2f2b2a)}
.learn-panel{position:absolute;left:137px;top:0;width:136px;height:122px;background:var(--teal-panel);color:#fff;padding:10px 0 0 15px}
.learn-panel h3{font-size:12px;font-weight:400}
.learn-panel .lead{font-size:7px;margin-top:3px}
.learn-panel ul{list-style:none;margin-top:6px}
.learn-panel li{font-size:6.3px;line-height:12.3px}
.learn-panel li::before{content:"›";margin-right:4px}
.learn-panel .more{position:absolute;left:74px;top:98px;width:52px;height:15px;border:1px solid #fff;font-size:6.5px;text-align:center;line-height:13px}

/* news */
.pager{top:754px;width:12px;height:12px;background:#8fd0ea;color:#fff;font-size:9px;text-align:center;line-height:11px}
.news{top:777px;width:208px}
.news .thumb{height:94px;position:relative}
.news .posted{position:absolute;left:0;bottom:1px;height:18px;padding:0 9px;background:var(--teal);color:#fff;font-size:7px;font-style:italic;line-height:18px}
.news h3{margin-top:17px;font-size:12.5px;font-weight:400;color:var(--accent)}
.news p{margin-top:6px;font-size:6.6px;line-height:12.2px;color:#666}
.news .read{display:block;margin-top:11px;width:63px;height:18px;background:linear-gradient(#2fb3ea,#1690cc);color:#fff;font-size:6px;text-align:center;line-height:18px}

/* footer */
.site-footer{left:0;top:990px;width:958px;height:180px;background:var(--footer);color:#fff}
.foot-col{position:absolute}
.foot-col h4{font-size:8.5px;font-weight:600;margin-bottom:3px}
.foot-col li{list-style:none;font-size:6.4px;line-height:15.2px}
.news-input{width:160px;height:17px;background:var(--footer-deep);border-bottom:1px solid #2a7595;font-size:6.4px;padding:4px 8px;margin-top:10px}
.send{position:absolute;left:111px;width:50px;height:16px;background:#555;font-size:7px;text-align:center;line-height:16px;margin-top:5px}
.social{position:absolute;left:678px;font-size:7px}
.social span.dot{display:inline-block;width:20px;height:20px;border-radius:50%;background:#2c6e95;vertical-align:middle;margin-right:3px}
.copyright{left:0;top:1170px;width:958px;height:30px;background:var(--footer-deep);color:#fff;font-size:6.4px;padding:11px 0 0 147px}
</style>
</head>
<body>

<header class="site-header">
  <a class="abs brand" href="#">TAVO Sphere</a>
  <nav class="main-nav">
    <a href="#" style="left:338px">LEARN</a>
    <a href="#" style="left:399px">ABOUT</a>
    <a href="#" style="left:462px">CONTRIBUTE</a>
  </nav>
  <div class="abs search">SEARCH :
    <svg width="12" height="12" viewBox="0 0 12 12"><circle cx="5" cy="5" r="3.5" fill="none" stroke="#999" stroke-width="1.3"/><line x1="7.5" y1="7.5" x2="11" y2="11" stroke="#999" stroke-width="1.6"/></svg>
  </div>
  <a class="abs btn-top" href="#" style="left:687px">LOGIN</a>
  <a class="abs btn-top" href="#" style="left:754px">SIGNUP</a>
</header>

<section class="abs hero" role="img" aria-label="Photo of a smiling young woman lying on a lawn with a laptop, yellow flowers behind her"></section>
<a class="abs hero-arrow" href="#" style="left:79px" aria-label="Previous slide"><svg width="12" height="18" viewBox="0 0 12 18"><polyline points="10,2 3,9 10,16" fill="none" stroke="#bbb" stroke-width="1.5"/></svg></a>
<a class="abs hero-arrow" href="#" style="left:833px" aria-label="Next slide"><svg width="12" height="18" viewBox="0 0 12 18"><polyline points="2,2 9,9 2,16" fill="none" stroke="#bbb" stroke-width="1.5"/></svg></a>

<article class="abs category" style="left:144px">
  <h2>WORD LEARNING</h2>
  <p>Lorem Ipsum is simply dummy text of the printing and typesetting industry.</p>
  <a class="go" href="#"><svg width="12" height="14" viewBox="0 0 12 14"><polyline points="3,2 9,7 3,12" fill="none" stroke="#fff" stroke-width="2.6"/></svg></a>
</article>
<article class="abs category" style="left:368px">
  <h2>BASIC SENTENCE LEARNING</h2>
  <p>Lorem Ipsum is simply dummy text of the printing and typesetting industry.</p>
  <a class="go" href="#"><svg width="12" height="14" viewBox="0 0 12 14"><polyline points="3,2 9,7 3,12" fill="none" stroke="#fff" stroke-width="2.6"/></svg></a>
</article>
<article class="abs category" style="left:592px">
  <h2>CLASSIC STORIES</h2>
  <p>Lorem Ipsum is simply dummy text of the printing and typesetting industry.</p>
  <a class="go" href="#"><svg width="12" height="14" viewBox="0 0 12 14"><polyline points="3,2 9,7 3,12" fill="none" stroke="#fff" stroke-width="2.6"/></svg></a>
</article>

<section class="abs mission">
  <h1>We are non profit english learning online platform.</h1>
  <p>Lorem Ipsum is simply dummy text of the printing and typesetting industry. Lorem Ipsum has been the industry's standard dummy text ever since the 1500s</p>
</section>
<a class="abs btn-join" href="#">JOIN FOR LEARNING</a>

<h2 class="abs section-title" style="left:144px;top:584px">Welcome to TAVO Sphere</h2>
<div class="abs photo" style="left:144px;top:614px;width:185px;height:102px" role="img" aria-label="Photo of a cheerful young woman at a laptop"></div>
<p class="abs welcome-text">Lorem Ipsum is simply dummy text of the printing and typesetting industry. Lorem Ipsum has been the industry's standard dummy text ever since the 1500s, when an unknown printer took a galley of type and scrambled it to make a type specimen book. It has survived not only five centuries, but also the leap into electronic typesetting, remaining essentially unchanged.</p>

<aside class="abs learn-card">
  <div class="learn-photo" role="img" aria-label="Photo of students with headsets at computers in a classroom"></div>
  <div class="learn-panel">
    <h3>LEARN</h3>
    <p class="lead">Lorem Ipsum is simply dummy...</p>
    <ul>
      <li>WORD LEARNING</li>
      <li>BASIC SENTENCE LEARNING</li>
      <li>CLASSIC SHORT STORIES</li>
      <li>PICTURE DICTIONARY</li>
    </ul>
    <a class="more" href="#">READ MORE</a>
  </div>
</aside>

<h2 class="abs section-title" style="left:143px;top:740px">Latest news</h2>
<a class="abs pager" href="#" style="left:783px">‹</a>
<a class="abs pager" href="#" style="left:800px">›</a>

<article class="abs news" style="left:144px">
  <div class="thumb" role="img" aria-label="Photo of business people in a bright office" style="background:linear-gradient(100deg,#e9e9e9,#9a9a9a 40%,#6d7488 70%,#e4e2de)"><span class="posted">Posted on : 27 jun 2013</span></div>
  <h3>Basic sentence learning</h3>
  <p>Lorem Ipsum is simply dummy text of the printing and typesetting industry. Lorem Ipsum has been the industry's standard dummy text ever since the 1500s...</p>
  <a class="read" href="#">READ MORE</a>
</article>
<article class="abs news" style="left:376px">
  <div class="thumb" role="img" aria-label="Photo of a young man with headphones relaxing on a white sofa" style="background:linear-gradient(100deg,#f1efea,#dcd8d0 45%,#6a6a6a 75%,#d8d6d0)"><span class="posted">Posted on : 27 jun 2013</span></div>
  <h3>Basic sentence learning</h3>
  <p>Lorem Ipsum is simply dummy text of the printing and typesetting industry. Lorem Ipsum has been the industry's standard dummy text ever since the 1500s...</p>
  <a class="read" href="#">READ MORE</a>
</article>
<article class="abs news" style="left:606px">
  <div class="thumb" role="img" aria-label="Photo of a group of students studying outdoors" style="background:linear-gradient(100deg,#5f7f3a,#c04a3a 35%,#b48d74 60%,#3b4a2a)"><span class="posted">Posted on : 27 jun 2013</span></div>
  <h3>Basic sentence learning</h3>
  <p>Lorem Ipsum is simply dummy text of the printing and typesetting industry. Lorem Ipsum has been the industry's standard dummy text ever since the 1500s...</p>
  <a class="read" href="#">READ MORE</a>
</article>

<footer class="abs site-footer">
  <div class="foot-col" style="left:145px;top:13px">
    <h4>WELCOME</h4>
    <ul><li>HELP</li><li>CONTACT US</li><li>FOR TEACHERS</li><li>VOLUNTEER</li><li>CONTRIBUTORS</li><li>JOBS</li><li>BLOG</li><li>USER STORIES</li></ul>
  </div>
  <div class="foot-col" style="left:275px;top:13px">
    <h4>LEARN</h4>
    <ul><li>WORD LEARNING</li><li>BASIC SENTENCE LEARNING</li><li>CLASSIC SHORT STORIES</li><li>PICTURE DICTIONARY</li></ul>
    <h4 style="margin-top:5px">ABOUT</h4>
    <ul><li>ABOUT TAVO SPHERE</li><li>TEAM</li><li>SUPPORTERS</li><li>CONTRIBUTORS</li></ul>
  </div>
  <div class="foot-col" style="left:432px;top:20px">
    <h4>CONTRIBUTE</h4>
    <ul><li>DONATE</li><li>VOLUNTEER</li></ul>
    <h4 style="margin-top:12px">NEWSLETTER SIGNUP</h4>
    <ul><li>GET OUR RECENT UPDATES THROUGH YOUR EMAIL :</li></ul>
    <div class="news-input" style="margin-left:1px">ENTER YOUR EMAIL D :</div>
    <a class="send" href="#">SEND</a>
  </div>
  <div class="social" style="top:19px"><span class="dot"></span>: CIRCLEPAGE</div>
  <div class="social" style="top:46px"><span class="dot"></span>: CHIRPLINE</div>
  <div class="social" style="top:73px"><span class="dot"></span>: WORKNET</div>
</footer>
<div class="abs copyright">COPYRIGHT 2013 TAVO SPHERE. ALL RIGHTS RESERVED.</div>

</body>
</html>
```